Rovelux

Hi everyone!

Looks like our project is more sophisticated than we expected. So good news - we increased the budget! and one of you will sure get the prize - no money back for us!

We are a young Russian company that specializes in in-taxi entertainment. We believe that our key strength is great attention to user experience. We've devoted much effort to improve ergonomics of our devices - tablet PCs that we install in the taxis. And yes, we enjoy to simplify things!

Now we need the most basic things - a logo and some staff for client meetings (primarily advertisers and ad agencies).

As for logo - we already have one engraved on the prototypes of our device (see attached file). This is one of the ideas (still far from perfect) - what we appreciate in it is minimalistic yet stylish approach.

As for "take it to the meeting stuff" we want to start with name card, pen and notepad (A4) that we will leave in clients's office, also as a reminder. Shall your have more smart ideas - always welcome!

As for logo and name cards - we would like to make an image of serious but modern company. Our design should communicate creativity and reliability. We believe that "to understand is to simplify" - minimalistic design is the most difficult one. Its better to work hard on fonts and arrangement, than put 10 variegated images.

SO THE TASK IS TO DESIGN:
- a logo
- a name card
- a note pad (great example in attachment)
- a pen

Shall you have more questions - please ask in comments.

We look forward to meeting like-minded fellows here!
Updates

Target Market(s)

Out target are:

- advertiser
- advertising agencies
- taxi passenger

Industry/Entity Type

It Company

Requirements
Must have
• font should be chosen very carefully
Nice to have
• classic minimalistic plain text only but very stylish name card is a dream of one of our co-founders:)
Should not have
• we do not want to have taxi-like colors and chess-boards. We are closer to "innovation", "entertainment", and "user experience", rather than "taxi".

```html
<!DOCTYPE html>
<html lang="en">
<head>
<meta charset="utf-8">
<title>Rovelux – name and notepad</title>
<link rel="stylesheet" href="https://fonts.googleapis.com/css2?family=Didact+Gothic&display=swap">
<style>
  :root {
    --ink: #231f20;
    --paper: #ffffff;
    --stage: #d5dde3;
    --grid: #d9d9d9;
    --meta: #3a3a3a;
  }
  * { margin: 0; padding: 0; box-sizing: border-box; }
  html, body { width: 1200px; height: 1000px; overflow: hidden; }
  body {
    position: relative;
    background: var(--paper);
    font-family: "Didact Gothic", "Helvetica Neue", Arial, sans-serif;
    color: var(--ink);
  }
  .name-row {
    position: absolute; left: 0; top: 0; width: 1200px; height: 233px;
    background: var(--paper);
  }
  .brand-name {
    position: absolute;
    display: flex; align-items: center; justify-content: center;
    font-size: 96px; line-height: 1; letter-spacing: -1px;
  }
  .brand-name--light { left: 135px; top: 60px; width: 400px; height: 122px; color: var(--ink); }
  .brand-name--dark {
    left: 633px; top: 60px; width: 432px; height: 122px;
    background: var(--ink); color: var(--paper);
  }

  .stage {
    position: absolute; left: 0; top: 233px; width: 1200px; height: 767px;
    background: var(--stage);
  }
  .variant-label {
    position: absolute; top: 48px; font-size: 19px; color: var(--ink);
  }
  .notepad {
    position: absolute; top: 44px; width: 480px; height: 678px;
    background: var(--paper);
    box-shadow: 0 0 4px rgba(0,0,0,0.18);
  }
  .notepad__grid {
    position: absolute; left: 0; top: 0; width: 480px; height: 632px;
    background-image:
      linear-gradient(to right, var(--grid) 1px, transparent 1px),
      linear-gradient(to bottom, var(--grid) 1px, transparent 1px);
    background-size: 11.7px 11.7px;
  }
  .notepad__footer {
    position: absolute; left: 12px; right: 10px; top: 641px; height: 30px;
  }
  .contact {
    font-size: 7.8px; line-height: 11px; color: var(--meta); letter-spacing: 0.2px;
  }
  .footer-name {
    position: absolute; right: 0; top: -2px;
    display: flex; align-items: center; justify-content: center;
    width: 99px; height: 28px;
    font-size: 19px; line-height: 1; letter-spacing: -0.3px;
  }
  .footer-name--plate { background: var(--ink); color: var(--paper); }
  .footer-name--plain { color: var(--ink); }
</style>
</head>
<body>
  <section class="name-row">
    <div class="brand-name brand-name--light">rovelux</div>
    <div class="brand-name brand-name--dark">rovelux</div>
  </section>

  <section class="stage">
    <span class="variant-label" style="left:64px">1</span>
    <article class="notepad" style="left:93px">
      <div class="notepad__grid"></div>
      <footer class="notepad__footer">
        <p class="contact">Kazan, Ulitsa Sadovaya, 12<br>
          tel: +7 843 555 01 27 • mob: +7 917 555 62 08<br>
          roveluxmedia.com • e-mail: hello@roveluxmedia.com</p>
        <div class="footer-name footer-name--plate">rovelux</div>
      </footer>
    </article>

    <span class="variant-label" style="left:593px">2</span>
    <article class="notepad" style="left:628px">
      <div class="notepad__grid"></div>
      <footer class="notepad__footer">
        <p class="contact">Kazan, Ulitsa Sadovaya, 12<br>
          tel: +7 843 555 01 27 • mob: +7 917 555 62 08<br>
          roveluxmedia.com • e-mail: hello@roveluxmedia.com</p>
        <div class="footer-name footer-name--plain">rovelux</div>
      </footer>
    </article>
  </section>
</body>
</html>
```